Harbor Lantern's Chinese/Dim Sum Restaurant Menu

Harbor Lantern's is a seafood-asian fusion restaurant featuring dim sum and other classical asian fusion items.

We need a menu design that includes both our food menu and our drink menu.

Food menu: Needs to have space for descriptions of food (please just include a place holder and we will input them later). See attached for food menu items.

Drink menu: Just lists of items with prices. See attached Jade Meadow Menu- please include the same items, but rebrand for Harbor Lantern's.

The menus must be able to be printed in a 4.25x11in paper.

We want something modern and contemporary. My boss likes geometrical design aspects and minimalism. So, nothing too ornate. But, it has to be different from the Jade Meadow menus. Colors can be black, red, gold or blue- but it must be able to be tied into our black and red Harbor Lantern's logo. Including elements of Chinese culture, especially fishing, is a plus, but not necessary.

We also need this in ai format when we download final copy so we can edit in the future.

UPDATE: Please note, we already have a logo.

Target Market(s)

Upscale family diners

Industry/Entity Type

Chinese Food

Font styles to use
Serif
Sans Serif

Colors
0054AA
0677BA
7BADD7
CADEEF
E8F1F8
0094D4
00A9DD
6FCCEA
C7EBF8
E9F6FB
FFC000
F8CF3A
FAE287
FDF2CF
FEFAEE
EB3D1F
EC4F4E
F09395
F8D3D4
FCEDEE

Requirements
Must have
• Classic, minimalist, elegant

```html
<!DOCTYPE html>
<html lang="en">
<head>
<meta charset="utf-8">
<title>Harbor Lantern's Dim Sum Menu</title>
<link href="https://fonts.googleapis.com/css2?family=Playfair+Display:ital,wght@0,700;0,900;1,600&family=Kaushan+Script&family=Lato:wght@400;700&display=swap" rel="stylesheet">
<style>
:root{
  --red:#D92A27;
  --red-dark:#B51F1C;
  --gold:#F8CF3A;
  --gold-soft:#FAE287;
  --ink:#1E1E1E;
  --muted:#6B6B6B;
  --paper:#FFFFFF;
  --canvas:#FFFFFF;
  --blush:#FCEDEE;
  --sky:#E8F1F8;
}
*{margin:0;padding:0;box-sizing:border-box}
html,body{width:1200px;height:3728px;overflow:hidden;background:var(--canvas)}
body{position:relative;font-family:'Lato',sans-serif;color:var(--ink)}
.panel{position:absolute;width:456px;background:var(--paper);box-shadow:0 2px 10px rgba(0,0,0,.18);overflow:hidden;padding:40px 34px 40px}
.panel::before,.panel::after{content:"";position:absolute;left:0;right:0;height:16px;background:var(--red);border-bottom:3px solid var(--gold)}
.panel::before{top:0}
.panel::after{bottom:0;border-bottom:none;border-top:3px solid var(--gold)}
.p1{left:118px;top:40px;height:1120px}
.p2{left:626px;top:100px;height:1060px}
.p3{left:118px;top:1320px;height:1120px}
.p4{left:626px;top:1320px;height:1120px}
.p5{left:118px;top:2540px;height:1140px}
.p6{left:626px;top:2540px;height:1140px}

.brand{display:flex;align-items:center;justify-content:center;gap:10px;margin-top:30px}
.brand-dot{width:22px;height:22px;border-radius:50%;background:var(--red)}
.brand-name{font-family:'Playfair Display',serif;font-weight:900;font-size:34px;color:var(--red)}
.cover-title{font-family:'Kaushan Script',cursive;text-align:center;color:var(--ink);line-height:.95;margin-top:40px}
.cover-title .l1{display:block;font-size:58px;color:var(--red)}
.cover-title .l2{display:block;font-size:92px}

.art{border-radius:6px}
.art-dumplings{height:300px;margin:24px -34px 20px;background:radial-gradient(circle at 50% 50%,#F3E2C3 0,#E9C99A 40%,#C99A63 70%,#fff 100%)}

.head{display:inline-block;background:var(--red);color:#fff;font-family:'Playfair Display',serif;font-style:italic;font-weight:600;font-size:17px;padding:4px 24px 5px 18px;margin:14px 0 8px;clip-path:polygon(0 0,100% 0,92% 50%,100% 100%,0 100%)}
.sub{font-size:10px;font-weight:700;letter-spacing:.1em;color:var(--red);margin:6px 0 3px}
.items{list-style:none}
.items li{display:flex;justify-content:space-between;align-items:center;font-size:11.5px;line-height:17px}
.price{background:var(--red);color:#fff;font-size:9px;font-weight:700;min-width:26px;text-align:center;line-height:12px;padding:0 3px}
.small li{font-size:10px;line-height:14px}
.small .price{font-size:8px;min-width:22px;line-height:10px}
.row{display:flex;gap:14px;align-items:flex-start}
.row .col{flex:1}
.row .art{flex:0 0 150px}
.desc{display:block;font-size:8.5px;color:var(--muted);line-height:11px}
.items li.two{align-items:flex-start;margin-bottom:3px}
.art-bowl{height:160px;background:radial-gradient(circle,#F7D6B8,#E59A62 60%,#fff 72%)}
.art-soup{height:150px;background:radial-gradient(circle,#F5E6C8,#DDB27A 60%,#fff 72%)}
.art-green{height:140px;background:radial-gradient(circle,#DDEFC4,#8DBF63 60%,#fff 72%)}
.art-red{height:150px;background:radial-gradient(circle,#F8D3D4,#E07A6A 60%,#fff 72%)}
.art-wine{height:230px;background:linear-gradient(160deg,#F3E3EC,#B25D7E 60%,#fff)}
.art-beer{height:240px;background:linear-gradient(180deg,#E9F2DC,#6D9A4C 55%,#fff)}
.art-drink{height:200px;background:linear-gradient(180deg,#FCEDEE,#F09395 60%,#fff)}
.art-cocktail{height:260px;background:linear-gradient(180deg,#FEFAEE,#F8CF3A 40%,#EC4F4E 75%,#fff)}
.art-bottles{height:130px;background:linear-gradient(180deg,#FDF2CF,#C99A63 70%,#fff)}
.art-fruit{height:130px;background:radial-gradient(circle,#E9F6FB,#6FCCEA 55%,#fff 72%)}
</style>
</head>
<body>

<section class="panel p1">
  <div class="brand"><span class="brand-dot"></span><span class="brand-name">Harbor Lantern's</span></div>
  <h1 class="cover-title"><span class="l1">Dim Sum</span><span class="l2">MENU</span></h1>
  <div class="art art-dumplings" role="img" aria-label="Steamer baskets of dim sum dumplings"></div>
  <div class="row">
    <div class="col">
      <h2 class="head">Dim Sum</h2>
      <ul class="items">
        <li>Har Gow<span class="price">9</span></li>
        <li>Pineapple Dumplings<span class="price">8</span></li>
        <li>Lobster Dumpling<span class="price">12</span></li>
        <li>Shrimp Roll<span class="price">9</span></li>
        <li>Pork Ribs<span class="price">8</span></li>
        <li>Spicy Pork Ton<span class="price">8</span></li>
        <li>Vegan Spice Bun Tot<span class="price">7</span></li>
        <li>Pork Shu Mai Bao<span class="price">8</span></li>
        <li>Crab &amp; Pork Dumpling<span class="price">10</span></li>
        <li>BBQ Pork Bao<span class="price">8</span></li>
        <li>Sweet Corn Dumplings<span class="price">7</span></li>
      </ul>
    </div>
    <div class="art art-bowl" role="img" aria-label="Bowl of dumplings with chopsticks" style="margin-top:60px"></div>
  </div>
</section>

<section class="panel p2">
  <div class="row">
    <div class="col">
      <h2 class="head">Soup</h2>
      <ul class="items">
        <li>Cup Hot &amp; Sour Soup<span class="price">5</span></li>
        <li>Bowl Hot &amp; Sour Soup<span class="price">9</span></li>
        <li>Cup Egg Flower Soup<span class="price">5</span></li>
        <li>Bowl Egg Flower Soup<span class="price">9</span></li>
        <li>Wonton Soup<span class="price">9</span></li>
        <li>Bean Curd Wonton Soup<span class="price">9</span></li>
      </ul>
    </div>
    <div class="art art-soup" role="img" aria-label="Bowl of soup" style="margin-top:16px"></div>
  </div>
  <div class="row">
    <div class="col">
      <h2 class="head">Appetizer</h2>
      <ul class="items">
        <li>Walnut Shrimp<span class="price">14</span></li>
        <li>Chicken Lettuce Wrap<span class="price">12</span></li>
        <li>Tofu Lettuce Wrap<span class="price">11</span></li>
        <li>Crispy Noodle Salad<span class="price">10</span></li>
        <li>Edamame<span class="price">6</span></li>
        <li>Seaweed Roll<span class="price">8</span></li>
        <li>Crab Cheese Wonton<span class="price">9</span></li>
        <li>Tuna Tower<span class="price">15</span></li>
        <li>Ahi Tuna and Fish Crisps<span class="price">14</span></li>
        <li>Calamari<span class="price">12</span></li>
        <li>Sesame Sea Noodle Salad<span class="price">11</span></li>
        <li>Chinese Pancakes<span class="price">8</span></li>
        <li>Exotic Cucumber Salad<span class="price">7</span></li>
        <li>Steamed Salad<span class="price">7</span></li>
      </ul>
    </div>
    <div class="art art-red" role="img" aria-label="Plate of appetizers" style="margin-top:60px"></div>
  </div>
  <div class="row">
    <div class="col">
      <h2 class="head">Seafood</h2>
      <ul class="items">
        <li>Szechuan Lobster<span class="price">32</span></li>
        <li>Lobster Black Bean Sauce<span class="price">32</span></li>
        <li>Kung Pao Shrimp<span class="price">18</span></li>
        <li>Kung Pao Chicken<span class="price">16</span></li>
        <li>Kung Pao Tofu<span class="price">14</span></li>
        <li>Broccoli Chicken<span class="price">16</span></li>
        <li>Broccoli Beef<span class="price">18</span></li>
        <li>Broccoli Shrimp<span class="price">18</span></li>
        <li>Mongolian Beef<span class="price">19</span></li>
        <li>General Tso's Chicken<span class="price">16</span></li>
        <li>General Tso's Tofu<span class="price">14</span></li>
      </ul>
    </div>
    <div class="art art-bowl" role="img" aria-label="Seafood dish" style="margin-top:50px"></div>
  </div>
  <div class="row">
    <div class="col">
      <h2 class="head">Veggie</h2>
      <ul class="items">
        <li>Sauteed Green Beans<span class="price">11</span></li>
        <li>Sizzling Lettuce, Oyster Sauce<span class="price">11</span></li>
        <li>Broccoli Garlic Sauce<span class="price">11</span></li>
      </ul>
    </div>
    <div class="art art-green" role="img" aria-label="Green vegetable dish" style="height:100px;margin-top:14px"></div>
  </div>
</section>

<section class="panel p3">
  <div class="row">
    <div class="col">
      <h2 class="head">Rice &amp; Noodle</h2>
      <ul class="items">
        <li>Seafood Fried Rice<span class="price">16</span></li>
        <li>Veggie Fried Rice<span class="price">12</span></li>
        <li>Chicken Fried Rice<span class="price">14</span></li>
        <li>Beef Fried Rice<span class="price">15</span></li>
        <li>Seafood Chow Mein<span class="price">17</span></li>
        <li>Chicken Chow Mein<span class="price">14</span></li>
        <li>Beef Chow Mein<span class="price">15</span></li>
      </ul>
    </div>
    <div class="art art-bowl" role="img" aria-label="Bowl of noodles" style="margin-top:16px"></div>
  </div>
  <div class="row">
    <div class="col">
      <h2 class="head">Sweet &amp; Dessert</h2>
      <ul class="items">
        <li>Chocolate Dumpling<span class="price">8</span></li>
        <li>Sweet Egg Bun<span class="price">7</span></li>
        <li>Mochi Ice<span class="price">7</span></li>
      </ul>
    </div>
    <div class="art art-red" role="img" aria-label="Sweet buns" style="height:100px;margin-top:14px"></div>
  </div>
  <div class="row">
    <div class="col">
      <h2 class="head">Wine</h2>
      <p class="sub">WHITE BY THE GLASS</p>
      <ul class="items small">
        <li>Long Island Pinot Grigio<span class="price">11</span></li>
        <li>Riverbend Sauvignon Blanc<span class="price">12</span></li>
        <li>Coastal Chardonnay<span class="price">12</span></li>
        <li>Northern Riesling<span class="price">11</span></li>
        <li>Valley Moscato<span class="price">10</span></li>
        <li>Orchard Rosé<span class="price">11</span></li>
        <li>Fruit Sangria<span class="price">10</span></li>
      </ul>
      <p class="sub">RED BY THE GLASS</p>
      <ul class="items small">
        <li>Southern Pinot Noir<span class="price">13</span></li>
        <li>Hillside Merlot<span class="price">12</span></li>
        <li>Ridge Cabernet Sauvignon<span class="price">14</span></li>
        <li>Estate Malbec<span class="price">12</span></li>
        <li>Old Vine Zinfandel<span class="price">13</span></li>
        <li>Hazelnut Red Blend<span class="price">12</span></li>
        <li>Mountain Syrah<span class="price">13</span></li>
        <li>Cellar Tempranillo<span class="price">12</span></li>
        <li>Sparkling Brut<span class="price">12</span></li>
      </ul>
    </div>
    <div class="art art-wine" role="img" aria-label="Wine bottle and glass" style="margin-top:40px"></div>
  </div>
  <div class="row">
    <div class="col">
      <h2 class="head">Tea</h2>
      <ul class="items">
        <li>Hibiscus Rose Tea<span class="price">5</span></li>
        <li>Jasmine Green Tea<span class="price">5</span></li>
        <li>Oolong Tea<span class="price">5</span></li>
        <li>Lemon Honey Tea<span class="price">5</span></li>
      </ul>
    </div>
    <div class="art art-drink" role="img" aria-label="Glass of iced tea" style="height:110px;margin-top:14px"></div>
  </div>
</section>

<section class="panel p4">
  <div class="row">
    <div class="col">
      <h2 class="head">Bottled Beer</h2>
      <ul class="items small">
        <li>Harbor Lager<span class="price">7</span></li>
        <li>Northstar Lager<span class="price">7</span></li>
        <li>Golden Rice Beer<span class="price">7</span></li>
        <li>Coastal Pale Ale<span class="price">7</span></li>
        <li>Dragon IPA<span class="price">8</span></li>
        <li>Lantern Light<span class="price">6</span></li>
        <li>Amber Wheat<span class="price">7</span></li>
        <li>River Stout<span class="price">8</span></li>
        <li>Citrus Pilsner<span class="price">7</span></li>
        <li>Summit Porter<span class="price">8</span></li>
        <li>Cove Hazy IPA<span class="price">8</span></li>
        <li>Apple Cider<span class="price">7</span></li>
        <li>Ginger Beer<span class="price">6</span></li>
        <li>Non-Alcoholic Lager<span class="price">5</span></li>
      </ul>
    </div>
    <div class="art art-beer" role="img" aria-label="Beer bottle and glass" style="margin-top:20px"></div>
  </div>
  <div class="row">
    <div class="col">
      <h2 class="head">Wine</h2>
      <ul class="items small">
        <li>Rosé Sparkling Bottle<span class="price">42</span></li>
        <li>Brut Sparkling Bottle<span class="price">40</span></li>
        <li>Sauvignon Blanc Bottle<span class="price">44</span></li>
        <li>Pinot Grigio Bottle<span class="price">40</span></li>
        <li>Chardonnay Bottle<span class="price">46</span></li>
        <li>Riesling Bottle<span class="price">40</span></li>
        <li>Moscato Bottle<span class="price">38</span></li>
        <li>Rosé Bottle<span class="price">40</span></li>
        <li>Pinot Noir Bottle<span class="price">50</span></li>
        <li>Merlot Bottle<span class="price">46</span></li>
        <li>Cabernet Bottle<span class="price">56</span></li>
        <li>Malbec Bottle<span class="price">46</span></li>
        <li>Zinfandel Bottle<span class="price">48</span></li>
        <li>Red Blend Bottle<span class="price">46</span></li>
        <li>Syrah Bottle<span class="price">48</span></li>
        <li>Champagne Split<span class="price">18</span></li>
        <li>Plum Wine<span class="price">10</span></li>
      </ul>
    </div>
    <div class="art art-wine" role="img" aria-label="Wine glasses" style="margin-top:40px"></div>
  </div>
  <div class="row">
    <div class="col">
      <h2 class="head">Desserts</h2>
      <ul class="items">
        <li>Plum Moonflower<span class="price">9</span></li>
        <li>Pineapple Coconut Ice<span class="price">9</span></li>
        <li>Toffee Coconut Ice Cream<span class="price">8</span></li>
        <li>Mandarin Sorbet<span class="price">7</span></li>
        <li>Vanilla Ice Cream<span class="price">6</span></li>
      </ul>
    </div>
    <div class="art art-fruit" role="img" aria-label="Fruit dessert" style="margin-top:14px"></div>
  </div>
</section>

<section class="panel p5">
  <div class="row">
    <div class="col">
      <h2 class="head">Liquor</h2>
      <p class="sub">VODKA</p>
      <ul class="items small">
        <li>Silver Heron<span class="price">11</span></li>
        <li>Citron Heron<span class="price">11</span></li>
        <li>North Birch<span class="price">9</span></li>
        <li>Tidewater<span class="price">9</span></li>
        <li>Harbor Well<span class="price">7</span></li>
        <li>Frost Peak<span class="price">10</span></li>
        <li>Blue Steppe<span class="price">10</span></li>
        <li>Vanilla Reed<span class="price">9</span></li>
        <li>Orchard Pear<span class="price">9</span></li>
      </ul>
      <p class="sub">RUM</p>
      <ul class="items small">
        <li>Island Gold<span class="price">9</span></li>
        <li>Cove Spiced<span class="price">9</span></li>
        <li>Coconut Bay<span class="price">8</span></li>
        <li>Dark Reef<span class="price">10</span></li>
        <li>Harbor Well Rum<span class="price">7</span></li>
      </ul>
      <p class="sub">LIQUEURS</p>
      <ul class="items small">
        <li>Amaretto<span class="price">9</span></li>
        <li>Coffee Liqueur<span class="price">9</span></li>
        <li>Irish Cream<span class="price">9</span></li>
        <li>Orange Liqueur<span class="price">10</span></li>
        <li>Peach Schnapps<span class="price">8</span></li>
        <li>Melon Liqueur<span class="price">8</span></li>
        <li>Lychee Liqueur<span class="price">9</span></li>
        <li>Sambuca<span class="price">9</span></li>
      </ul>
      <p class="sub">GIN</p>
      <ul class="items small">
        <li>Dry Botanical<span class="price">10</span></li>
        <li>Cucumber Rose<span class="price">11</span></li>
        <li>Harbor Well Gin<span class="price">7</span></li>
        <li>Old Tom<span class="price">10</span></li>
      </ul>
      <div class="art art-bottles" role="img" aria-label="Liquor bottles" style="margin-top:14px"></div>
    </div>
    <div class="col" style="flex:1">
      <p class="sub" style="margin-top:18px">TEQUILA</p>
      <ul class="items small">
        <li>Casa Alta Silver<span class="price">12</span></li>
        <li>Casa Alta Reposado<span class="price">13</span></li>
        <li>Casa Alta Añejo<span class="price">15</span></li>
        <li>Agave Blanco<span class="price">10</span></li>
        <li>Agave Reposado<span class="price">11</span></li>
        <li>Desert Sun<span class="price">9</span></li>
        <li>Mezcal Joven<span class="price">12</span></li>
      </ul>
      <p class="sub">WHISKEY</p>
      <ul class="items small">
        <li>Highland Crest Red<span class="price">10</span></li>
        <li>Highland Crest Black<span class="price">13</span></li>
        <li>Glen Harbor 12<span class="price">15</span></li>
        <li>Glen Harbor 18<span class="price">24</span></li>
        <li>Kentucky Oak<span class="price">11</span></li>
        <li>Copper Still Rye<span class="price">12</span></li>
        <li>Irish Meadow<span class="price">10</span></li>
        <li>Tennessee Ember<span class="price">10</span></li>
        <li>Japanese Blend<span class="price">14</span></li>
        <li>Honey Barrel<span class="price">10</span></li>
        <li>Small Batch Bourbon<span class="price">13</span></li>
      </ul>
      <p class="sub">COGNAC</p>
      <ul class="items small">
        <li>Maison Delune VS<span class="price">13</span></li>
        <li>Maison Delune VSOP<span class="price">16</span></li>
        <li>Maison Delune XO<span class="price">28</span></li>
      </ul>
      <p class="sub">SAKE</p>
      <ul class="items small">
        <li>Junmai Hot<span class="price">9</span></li>
        <li>Junmai Ginjo<span class="price">12</span></li>
        <li>Nigori Cloudy<span class="price">11</span></li>
        <li>Sparkling Sake<span class="price">12</span></li>
        <li>Plum Sake<span class="price">10</span></li>
        <li>Soju<span class="price">9</span></li>
      </ul>
      <div class="art art-drink" role="img" aria-label="Liquor bottle and glass" style="height:150px;margin-top:14px"></div>
    </div>
  </div>
</section>

<section class="panel p6">
  <div class="row">
    <div class="col">
      <h2 class="head">Cocktail</h2>
      <ul class="items small">
        <li class="two"><span>Pineapple Mojito<span class="desc">Rum, mint, pineapple, lime</span></span><span class="price">12</span></li>
        <li class="two"><span>Elderflower Spritz<span class="desc">Gin, elderflower, prosecco</span></span><span class="price">12</span></li>
        <li class="two"><span>Whiskey Sweet Blackberry<span class="desc">Bourbon, blackberry, lemon</span></span><span class="price">13</span></li>
        <li class="two"><span>Lychee Martini<span class="desc">Vodka, lychee, lime</span></span><span class="price">12</span></li>
        <li class="two"><span>Jack &amp; Jin<span class="desc">Whiskey, ginger, honey</span></span><span class="price">12</span></li>
        <li class="two"><span>Ruby Margarita<span class="desc">Tequila, blood orange, agave</span></span><span class="price">13</span></li>
        <li class="two"><span>Lantern Mule<span class="desc">Vodka, ginger beer, lime</span></span><span class="price">12</span></li>
        <li class="two"><span>Whiskey Smash<span class="desc">Bourbon, mint, lemon</span></span><span class="price">12</span></li>
        <li class="two"><span>Plum Punch<span class="desc">Rum, plum wine, citrus</span></span><span class="price">12</span></li>
        <li class="two"><span>Coconut Breeze<span class="desc">Rum, coconut, pineapple</span></span><span class="price">12</span></li>
        <li class="two"><span>Lemongrass Collins<span class="desc">Gin, lemongrass, soda</span></span><span class="price">12</span></li>
        <li class="two"><span>Tequila Sunset<span class="desc">Tequila, orange, grenadine</span></span><span class="price">12</span></li>
        <li class="two"><span>Cucumber Cooler<span class="desc">Gin, cucumber, basil</span></span><span class="price">12</span></li>
        <li class="two"><span>Ginger Old Fashioned<span class="desc">Rye, ginger, bitters</span></span><span class="price">14</span></li>
        <li class="two"><span>Sake Sangria<span class="desc">Sake, peach, berries</span></span><span class="price">12</span></li>
        <li class="two"><span>Spicy Paloma<span class="desc">Tequila, grapefruit, chili</span></span><span class="price">13</span></li>
        <li class="two"><span>Midnight Espresso<span class="desc">Vodka, coffee, cream</span></span><span class="price">13</span></li>
        <li class="two"><span>Crimson Fizz<span class="desc">Gin, hibiscus, lemon</span></span><span class="price">12</span></li>
      </ul>
    </div>
    <div class="art art-cocktail" role="img" aria-label="Colourful cocktails in glasses" style="margin-top:40px;height:380px"></div>
  </div>
  <div class="row">
    <div class="col">
      <h2 class="head">Mocktails</h2>
      <ul class="items small">
        <li class="two"><span>Fruit Moonflower<span class="desc">Passion fruit, lime, soda</span></span><span class="price">7</span></li>
        <li class="two"><span>Lychee Cooler<span class="desc">Lychee, mint, tonic</span></span><span class="price">7</span></li>
        <li class="two"><span>Mango Sunrise<span class="desc">Mango, orange, grenadine</span></span><span class="price">7</span></li>
        <li class="two"><span>Berry Fizz<span class="desc">Berries, lemon, soda</span></span><span class="price">7</span></li>
        <li class="two"><span>Ginger Lemonade<span class="desc">Ginger, lemon, honey</span></span><span class="price">6</span></li>
        <li class="two"><span>Cucumber Mint Spritz<span class="desc">Cucumber, mint, lime</span></span><span class="price">6</span></li>
      </ul>
    </div>
    <div class="art art-drink" role="img" aria-label="Row of mocktail glasses" style="height:220px;margin-top:30px"></div>
  </div>
</section>

</body>
</html>
```